Marta's Dwellings website

We need a simple website for our property investment business in the UK. We basically need our contact details and brief description.We have the company logo already done (via ArtFlockly) so please use these:https://drive.google.com/drive/folders/1szJ3iRhelElZ40NIFT7w-c14MaY3Y_oV?usp=sharingYou could use some stock photos of UK houses for now.Let me know when to provide more detailed descriptions, etc

Coding

Coded - Design and coding required

Number of Pages Required

1 page

Colors

Designer to choose colors to be used in the design.

```html
<!DOCTYPE html>
<html lang="en">
<head>
<meta charset="utf-8">
<title>Marta's Dwellings</title>
<link href="https://fonts.googleapis.com/css2?family=Nunito+Sans:wght@400;600;700;800;900&display=swap" rel="stylesheet">
<style>
:root{
  --ink:#111111;
  --text:#2b2b2b;
  --muted:#555555;
  --paper:#ffffff;
  --shade:#f4f1f0;
  --rule:#9a9a9a;
  --sky:#4f86c9;
  --brick:#9a4b36;
  --map:#e8e6e3;
  --footer:#000000;
  --social:#2a6fd6;
}
*{margin:0;padding:0;box-sizing:border-box}
html,body{width:1200px;height:4187px;overflow:hidden}
body{position:relative;background:var(--paper);font-family:"Nunito Sans",Arial,sans-serif;color:var(--text)}
.abs{position:absolute}

/* header */
.brand{left:33px;top:16px;width:230px;height:112px;display:flex;flex-direction:column;align-items:center;justify-content:center;gap:12px;z-index:3}
.brand-mark{width:34px;height:34px;background:var(--ink)}
.brand-name{font-size:15px;font-weight:600;letter-spacing:6px;color:var(--ink);white-space:nowrap}
.nav{right:36px;top:26px;display:flex;gap:30px;z-index:3}
.nav a{font-size:13px;font-weight:600;color:var(--ink);text-decoration:none;padding:3px 10px}
.nav a.active{border:1.5px solid var(--ink)}

/* hero */
.hero{left:0;top:0;width:1200px;height:693px;z-index:1}
.hero-panel{left:699px;top:377px;width:355px;height:212px;background:rgba(0,0,0,.78);z-index:2;padding:22px 32px}
.hero-title{color:#fff;font-size:44px;font-weight:900;line-height:45px;letter-spacing:1px}
.btn-outline{display:inline-block;margin-top:26px;border:3px solid #fff;color:#fff;font-weight:800;font-size:17px;padding:10px 18px;outline:1px solid #444;outline-offset:2px}
.dots{left:520px;top:660px;width:130px;height:26px;background:rgba(0,0,0,.25);display:flex;gap:12px;align-items:center;justify-content:center;z-index:2}
.dots span{width:9px;height:9px;border-radius:50%;background:#bbb}
.dots span.on{background:#111}

/* stats */
.stats{left:0;top:693px;width:1200px;height:149px}
.stat{position:absolute;top:45px;width:200px;margin-left:-100px;text-align:center}
.stat b{display:block;font-size:23px;font-weight:800;color:var(--ink)}
.stat span{display:block;font-size:15px;color:var(--muted);margin-top:4px}
.stat-divider{position:absolute;top:42px;width:1px;height:68px;background:#ddd}

/* section title */
.section-title{width:1200px;left:0;text-align:center;font-size:31px;font-weight:800;color:var(--ink);letter-spacing:.5px}
.title-rule{left:574px;width:52px;height:4px;background:var(--rule)}

/* investments */
.invest{left:0;top:842px;width:1200px;height:630px;background:var(--shade)}
.card{top:1011px;width:300px;height:387px;background:#fff;border:2px solid #ddd}
.card-photo{width:100%;height:256px}
.card-body{padding:22px 26px 0}
.card-title{font-size:17px;font-weight:700;color:var(--ink)}
.card-address{font-size:12px;color:var(--text);margin-top:6px}
.card-meta{position:absolute;left:0;right:0;bottom:0;height:40px;border-top:2px solid #e4e4e4;display:flex;justify-content:space-between;align-items:center;padding:0 12px;font-size:11px;color:var(--text)}
.card-meta i{display:inline-block;width:12px;height:9px;background:#666;margin-right:6px;vertical-align:middle}

/* welcome */
.kicker-rule{left:146px;top:1638px;width:140px;height:2px;background:#777}
.kicker{left:146px;top:1657px;font-size:24px;color:var(--ink)}
.welcome-title{left:146px;top:1688px;font-size:42px;font-weight:800;color:var(--ink)}
.welcome-rule{left:146px;top:1749px;width:290px;height:3px;background:#777}
.copy{font-size:17px;line-height:23.3px;color:var(--text)}
.btn-solid{background:var(--ink);color:#fff;font-weight:800;font-size:16px;display:flex;align-items:center;justify-content:center}

/* property band */
.band{left:0;top:0;width:1200px;height:4187px;z-index:0}

/* how it works */
.step{top:3070px;width:292px;height:284px;background:#fff;border:2px solid #ccc;box-shadow:5px 5px 0 -1px #fff,6px 6px 0 0 #ccc;text-align:center;padding:106px 30px 0}
.step-icon{position:absolute;left:91px;top:-43px;width:110px;height:110px;border-radius:50%;background:var(--ink)}
.step h3{font-size:21px;font-weight:700;color:var(--ink);margin-top:-6px}
.step p{font-size:13.5px;line-height:19.5px;margin-top:14px;color:var(--text)}

/* contact */
.contact{left:719px;top:3431px;width:481px;height:470px;background:var(--shade)}
.contact h2{position:absolute;left:68px;top:62px;font-size:31px;font-weight:800;color:var(--ink)}
.contact-rule{position:absolute;left:68px;top:100px;width:50px;height:4px;background:var(--rule)}
.contact-name{position:absolute;left:118px;top:152px;font-size:18px;font-weight:800;color:#333}
.contact-addr{position:absolute;left:118px;top:186px;font-size:17px;line-height:25.8px;color:#333}

/* footer */
.footer-logo{left:130px;top:3930px;width:300px;height:120px;display:flex;flex-direction:column;align-items:center;justify-content:center;gap:18px;z-index:3}
.footer-logo .brand-mark{background:#fff;width:46px;height:46px}
.footer-logo .brand-name{color:#fff;font-size:17px;letter-spacing:8px}
.footer-divider{top:3902px;width:1px;height:148px;background:#555;z-index:3}
.footer-head{font-size:12px;font-weight:800;color:#fff;z-index:3;letter-spacing:.5px}
.footer-menu{left:644px;top:3934px;z-index:3;list-style:none}
.footer-menu li{font-size:10.5px;color:#fff;line-height:17.6px}
.social{left:940px;z-index:3;display:flex;align-items:center;gap:14px;font-size:11px;color:#fff}
.social i{width:26px;height:26px;border-radius:50%;background:var(--social)}
.footer-rule{left:78px;top:4105px;width:1044px;height:1px;background:#444;z-index:3}
.copyright{left:0;width:1200px;top:4146px;text-align:center;font-size:10.5px;color:#fff;z-index:3}
</style>
</head>
<body>

<!-- background bands and photo areas -->
<svg class="abs band" viewBox="0 0 1200 4187" aria-hidden="true">
  <defs>
    <linearGradient id="heroSky" x1="0" y1="0" x2="0" y2="1">
      <stop offset="0" stop-color="#2f6fc4"/>
      <stop offset=".35" stop-color="#6f8fb8"/>
      <stop offset="1" stop-color="#8a4d3b"/>
    </linearGradient>
    <linearGradient id="faint" x1="0" y1="0" x2="1" y2="0">
      <stop offset="0" stop-color="#e7e6e6"/>
      <stop offset="1" stop-color="#f2f1f1"/>
    </linearGradient>
  </defs>
  <!-- property investment faint backdrop -->
  <polygon points="0,2125 1200,2010 1200,2857 0,2810" fill="url(#faint)"/>
  <!-- footer -->
  <polygon points="0,3890 1200,3815 1200,4187 0,4187" fill="var(--footer)"/>
</svg>

<!-- header -->
<div class="abs brand"><span class="brand-mark"></span><span class="brand-name">MARTA'S DWELLINGS</span></div>
<nav class="abs nav">
  <a class="active">HOME</a><a>ABOUT US</a><a>SERVICES</a><a>INVESTMENT</a><a>BLOG</a><a>CONTACT US</a>
</nav>

<!-- hero -->
<svg class="abs hero" viewBox="0 0 1200 693" role="img" aria-label="Photo of a row of red-brick terraced houses under a blue sky">
  <polygon points="0,195 780,150 1200,135 1200,693 0,693" fill="url(#heroSky)"/>
</svg>
<div class="abs hero-panel">
  <div class="hero-title">PROPERTY<br>INVESTMENT</div>
  <span class="btn-outline">READ MORE</span>
</div>
<div class="abs dots"><span></span><span></span><span class="on"></span><span></span><span></span></div>

<!-- stats -->
<section class="abs stats">
  <div class="stat" style="left:198px"><b>23648</b><span>Investors count</span></div>
  <div class="stat-divider" style="left:280px"></div>
  <div class="stat" style="left:395px"><b>732</b><span>Number of funded loans</span></div>
  <div class="stat-divider" style="left:507px"></div>
  <div class="stat" style="left:600px"><b>40+</b><span>Properties Funded</span></div>
  <div class="stat-divider" style="left:698px"></div>
  <div class="stat" style="left:798px"><b>15</b><span>Years of Experience</span></div>
  <div class="stat-divider" style="left:898px"></div>
  <div class="stat" style="left:987px"><b>6524</b><span>Project Completed</span></div>
</section>

<!-- current investment -->
<section class="abs invest"></section>
<h2 class="abs section-title" style="top:896px">CURRENT INVESTMENT</h2>
<div class="abs title-rule" style="top:954px"></div>

<article class="abs card" style="left:130px">
  <div class="card-photo" role="img" aria-label="Photo of new-build brick houses beside a grass verge" style="background:linear-gradient(180deg,#5b93d6 0%,#9fbfe0 40%,#a55a3f 70%,#4f8a2b 100%)"></div>
  <div class="card-body"><div class="card-title">LOREM IPSUM</div><div class="card-address">14 Orchard Row, BRAMLEY, BX41 3QT</div></div>
  <div class="card-meta"><span><i></i>1Bedroom</span><span><i></i>1Bathroom</span><span><i></i>30 m²</span></div>
</article>
<article class="abs card" style="left:450px">
  <div class="card-photo" role="img" aria-label="Photo of a detached brick house with a white garage door" style="background:linear-gradient(180deg,#6aa0dc 0%,#b9c9d4 35%,#a8664a 65%,#6d8d3a 100%)"></div>
  <div class="card-body"><div class="card-title">LOREM IPSUM</div><div class="card-address">14 Orchard Row, BRAMLEY, BX41 3QT</div></div>
  <div class="card-meta"><span><i></i>1Bedroom</span><span><i></i>1Bathroom</span><span><i></i>30 m²</span></div>
</article>
<article class="abs card" style="left:772px">
  <div class="card-photo" role="img" aria-label="Photo of a red-brick family house with a front lawn" style="background:linear-gradient(180deg,#3f6fae 0%,#8ea8c6 35%,#9b543e 65%,#6f8f4a 100%)"></div>
  <div class="card-body"><div class="card-title">LOREM IPSUM</div><div class="card-address">14 Orchard Row, BRAMLEY, BX41 3QT</div></div>
  <div class="card-meta"><span><i></i>1Bedroom</span><span><i></i>1Bathroom</span><span><i></i>30 m²</span></div>
</article>

<!-- welcome -->
<div class="abs kicker-rule"></div>
<div class="abs kicker">WELCOME TO</div>
<h1 class="abs welcome-title">Marta's Dwellings</h1>
<div class="abs welcome-rule"></div>
<p class="abs copy" style="left:146px;top:1789px;width:372px">Lorem ipsum dolor sit amet, consectetur adipiscing elit, sed do eiusmod tempor incididunt ut labore et dolore magna aliqua. Ut enim ad minim veniam, quis nostrud exercitation ullamco laboris nisi ut aliquip ex ea commodo consequat. Duis aute irure dolor in reprehenderit in voluptate velit esse cillum dolore eu fugiat nulla pariatur. Excepteur sint occaecat.</p>
<div class="abs btn-solid" style="left:148px;top:2011px;width:150px;height:47px">READ MORE</div>
<div class="abs" role="img" aria-label="Photo of a brick bungalow extension with white windows and a hanging flower basket" style="left:576px;top:1545px;width:479px;height:565px;background:linear-gradient(180deg,#6c9ad4 0%,#b75c45 30%,#9a5a42 65%,#5c9a35 100%)"></div>

<!-- property investment -->
<div class="abs" role="img" aria-label="Photo of a tall red-brick house with timber detailing and white windows" style="left:141px;top:2185px;width:469px;height:623px;background:linear-gradient(180deg,#6fa3e0 0%,#a4553c 35%,#8e4533 75%,#c7c2bb 100%)"></div>
<h2 class="abs" style="left:670px;top:2266px;font-size:38px;font-weight:800;line-height:49px;color:var(--ink)">PROPERTY<br>INVESTMENT</h2>
<div class="abs" style="left:671px;top:2375px;width:146px;height:3px;background:var(--rule)"></div>
<p class="abs copy" style="left:671px;top:2423px;width:400px;line-height:25.6px">Lorem ipsum dolor sit amet, consectetur adipiscing elit, sed do eiusmod tempor incididunt ut labore et dolore magna aliqua. Ut enim ad minim veniam, quis nostrud exercitation ullamco laboris nisi ut aliquip ex ea commodo consequat. Duis aute irure dolor in reprehenderit in voluptate velit esse cillum dolore eu fugiat nulla pariatur. Excepteur sint occaecat.</p>
<div class="abs btn-solid" style="left:673px;top:2672px;width:150px;height:47px">READ MORE</div>

<!-- how it works -->
<h2 class="abs section-title" style="top:2902px">HOW DOES IT WORK?</h2>
<div class="abs title-rule" style="top:2964px"></div>

<article class="abs step" style="left:135px">
  <svg class="step-icon" viewBox="0 0 110 110" aria-hidden="true"><circle cx="55" cy="55" r="55" fill="#111"/><circle cx="55" cy="48" r="17" fill="none" stroke="#fff" stroke-width="5"/><path d="M30 78h50" stroke="#fff" stroke-width="6" stroke-linecap="round"/></svg>
  <h3>Borrower</h3>
  <p>Lorem ipsum dolor sit amet, consectetur adipiscing elit, sed do eiusmod tempor incididunt ut labore et dolore magna aliqua. Ut enim ad minim veniam.</p>
</article>
<article class="abs step" style="left:454px">
  <svg class="step-icon" viewBox="0 0 110 110" aria-hidden="true"><circle cx="55" cy="55" r="55" fill="#111"/><path d="M55 25l24 9v18c0 16-10 27-24 33-14-6-24-17-24-33V34z" fill="#fff"/><path d="M43 55l9 9 16-18" fill="none" stroke="#111" stroke-width="6" stroke-linecap="round" stroke-linejoin="round"/></svg>
  <h3>Security</h3>
  <p>Lorem ipsum dolor sit amet, consectetur adipiscing elit, sed do eiusmod tempor incididunt ut labore et dolore magna aliqua. Ut enim ad minim veniam.</p>
</article>
<article class="abs step" style="left:774px">
  <svg class="step-icon" viewBox="0 0 110 110" aria-hidden="true"><circle cx="55" cy="55" r="55" fill="#111"/><rect x="32" y="58" width="10" height="20" fill="#fff"/><rect x="47" y="46" width="10" height="32" fill="#fff"/><rect x="62" y="36" width="10" height="42" fill="#fff"/><circle cx="78" cy="72" r="10" fill="#fff"/></svg>
  <h3>Investor</h3>
  <p>Lorem ipsum dolor sit amet, consectetur adipiscing elit, sed do eiusmod tempor incididunt ut labore et dolore magna aliqua. Ut enim ad minim veniam.</p>
</article>

<!-- map and contact -->
<div class="abs" role="img" aria-label="Street map showing the office location" style="left:0;top:3431px;width:719px;height:470px;background:var(--map);clip-path:polygon(0 0,100% 0,100% 84%,0 100%)"></div>
<section class="abs contact">
  <h2>CONTACT US</h2>
  <div class="contact-rule"></div>
  <svg class="abs" style="left:70px;top:156px" width="24" height="36" viewBox="0 0 24 36" aria-hidden="true"><path d="M12 0C5 0 0 5 0 12c0 9 12 24 12 24s12-15 12-24C24 5 19 0 12 0z" fill="#aaa"/><circle cx="12" cy="12" r="5" fill="var(--shade)"/></svg>
  <div class="contact-name">MARTA LYNN CARROW</div>
  <div class="contact-addr">Unit 7, Harrow Court, 18-20<br>Fenwick Road, Ashby Vale,<br>Westhamshire,<br>United Kingdom,<br>WV14 6QR</div>
</section>

<!-- footer -->
<div class="abs footer-logo"><span class="brand-mark"></span><span class="brand-name">MARTA'S DWELLINGS</span></div>
<div class="abs footer-divider" style="left:530px"></div>
<div class="abs footer-divider" style="left:837px"></div>
<div class="abs footer-head" style="left:644px;top:3898px">MENU</div>
<ul class="abs footer-menu">
  <li>HOME</li><li>ABOUT US</li><li>SERVICES</li><li>INVESTMENT</li><li>BLOG</li><li>CONTACT US</li>
</ul>
<div class="abs footer-head" style="left:940px;top:3898px">CONNECT WITH US</div>
<div class="abs social" style="top:3935px"><i></i>Facepage</div>
<div class="abs social" style="top:3976px"><i></i>Chirper</div>
<div class="abs social" style="top:4016px"><i></i>Linkline</div>
<div class="abs footer-rule"></div>
<div class="abs copyright">Copyrights @ 2019 All Rights Reserved</div>

</body>
</html>
```